Upscale square business card for photographer

I need the logo I already own designed into a card that features a photo on one side and text on the other. I want a very upscale approach that can be printed on thick paper - maybe even letterpress.

Target Market(s)

Designers, artists, editors

Industry/Entity Type

Business

Contact Information for Business Card

Should be square and feature the text below

Font styles to use
Serif
Sans Serif

Requirements
Must have
• Following contact info:
• Dale Wickham
• 253-417-6924
• dale@dalewickham-example.com
Nice to have
• Mailing address
• 2967 Larkmere Ave. NW #158
• Marlow Bay, WA 98399
Should not have
• Should be monochrome - no color

```html
<!DOCTYPE html>
<html lang="en">
<head>
<meta charset="utf-8">
<title>Dale Wickham – Business Card</title>
<link href="https://fonts.googleapis.com/css2?family=Open+Sans:wght@400;600&display=swap" rel="stylesheet">
<style>
  :root {
    --backdrop: #e9e7e4;
    --card: #1c1c1d;
    --ink: #f4f4f4;
    --ink-soft: #e2e2e2;
    --wordmark: #4a4a4c;
    --rule: #ffffff;
    --photo-deep: #0b0b0c;
    --photo-mid: #2a2a2b;
  }
  * { box-sizing: border-box; margin: 0; padding: 0; }
  html, body {
    width: 1200px;
    height: 1000px;
    overflow: hidden;
    background: var(--backdrop);
    font-family: "Open Sans", Arial, sans-serif;
  }
  .stage { position: relative; width: 1200px; height: 1000px; }
  .card {
    position: absolute;
    left: 267px;
    width: 665px;
    height: 396px;
    background: var(--card);
    box-shadow: 0 6px 14px rgba(0,0,0,0.25);
  }
  .card--front { top: 75px; }
  .card--back { top: 534px; overflow: hidden; }

  .wordmark {
    position: absolute;
    right: 32px;
    top: 58px;
    text-align: right;
    color: var(--wordmark);
    font-weight: 600;
    font-size: 34px;
    letter-spacing: 5px;
    line-height: 1.15;
    text-transform: uppercase;
  }
  .wordmark__line { display: block; }

  .identity { position: absolute; left: 32px; top: 208px; color: var(--ink); }
  .identity__name { font-size: 21px; font-weight: 600; line-height: 1.2; }
  .identity__role { font-size: 16px; font-weight: 400; color: var(--ink-soft); margin-top: 2px; }

  .divider { position: absolute; left: 32px; top: 267px; width: 601px; height: 3px; }

  .contact {
    position: absolute;
    left: 32px;
    top: 285px;
    color: var(--ink);
    font-size: 16px;
    line-height: 24px;
    list-style: none;
  }
  .contact__address { margin-top: 13px; }

  .feature-photo {
    width: 100%;
    height: 100%;
    background: radial-gradient(ellipse 22% 40% at 50% 42%, var(--photo-mid) 0%, var(--photo-deep) 100%);
  }
</style>
</head>
<body>
<main class="stage">
  <section class="card card--front" aria-label="Card front">
    <div class="wordmark">
      <span class="wordmark__line">Dale Wickham</span>
      <span class="wordmark__line">Photography</span>
    </div>

    <div class="identity">
      <h1 class="identity__name">Dale Wickham</h1>
      <p class="identity__role">Photographer</p>
    </div>

    <svg class="divider" viewBox="0 0 601 3" aria-hidden="true">
      <rect x="0" y="0.5" width="601" height="1.5" fill="var(--rule)"/>
      <rect x="0" y="0" width="144" height="3" fill="var(--rule)"/>
    </svg>

    <ul class="contact">
      <li>253-417-6924</li>
      <li>dale@dalewickham-example.com</li>
      <li class="contact__address">2967 Larkmere Ave. NW #158 Marlow Bay, WA 98399</li>
    </ul>
  </section>

  <section class="card card--back" aria-label="Card back">
    <div class="feature-photo" role="img" aria-label="Black and white photograph of a white egret preening its wing, standing in dark still water"></div>
  </section>
</main>
</body>
</html>
```